Web Design Project for SEARCH ENGINE !

We need a website design for torrents search engine.

The Website will be www.Qentrova.com

Qentrova is a a search engine for torrents.
Qentrova search and index torrents results from all torrents sites.

We will need:
Logo
WebSite Design
slogen (optional)

we need only PSDs - no codded pages are needed !

Design to the following screen Size & resolution: 1024 x 768

***PLEASE DOWNLOAD ATTACHED FILE !

```html
<!DOCTYPE html>
<html lang="en">
<head>
<meta charset="utf-8">
<title>Qentrova – torrents search engine</title>
<link href="https://fonts.googleapis.com/css2?family=Questrial&family=Open+Sans:wght@400;600;700&display=swap" rel="stylesheet">
<style>
:root{
  --green:#1f9a3a;
  --green-light:#3cc35a;
  --ink:#222;
  --text:#333;
  --muted:#888;
  --line:#cfcfcf;
  --bar:#dedede;
  --bar-dark:#bdbdbd;
  --frame:#a9a9a9;
  --red:#d12a2a;
  --pink:#c0326a;
  --blue-badge:#1e9be0;
  --bg:#ffffff;
}
*{box-sizing:border-box;margin:0;padding:0}
html,body{width:1200px;height:900px;overflow:hidden;background:var(--bg)}
body{font-family:"Open Sans",Arial,sans-serif;color:var(--text)}
.canvas{position:relative;width:1200px;height:900px;overflow:hidden;background:linear-gradient(#f1f1f1,#fff 120px,#fff 820px,#e9e9e9)}
.abs{position:absolute}

.brand{left:117px;top:14px}
.brand-name{display:flex;align-items:center;gap:6px;font-family:"Questrial",sans-serif;font-size:50px;line-height:56px;color:var(--ink);letter-spacing:-1px}
.brand-dot{width:40px;height:40px;border-radius:50%;background:var(--green)}
.brand-tag{font-family:"Questrial",sans-serif;font-size:16px;color:var(--ink);margin-left:12px;margin-top:-4px}

.nav{left:460px;top:32px;display:flex;font-family:"Questrial",sans-serif;font-size:18px;color:var(--ink)}
.nav a{display:block;text-decoration:none;color:inherit;width:93px;text-align:center;height:24px;line-height:24px;white-space:nowrap}
.nav a.active{background:var(--green);color:#fff;position:relative;border-radius:2px}
.nav a.active::after{content:"";position:absolute;left:50%;bottom:-7px;margin-left:-7px;border:7px solid transparent;border-bottom:0;border-top-color:var(--green)}
.lang{left:930px;top:34px;font-size:12px;color:var(--ink);display:flex;align-items:center;gap:6px}
.lang-select{background:var(--green);color:#fff;width:62px;height:19px;padding-left:4px;line-height:19px;position:relative}
.lang-select::after{content:"";position:absolute;right:4px;top:6px;border:4px solid transparent;border-top:7px solid #fff;border-bottom:0}

.hero-frame{left:117px;top:91px;width:467px;height:243px;border:6px solid var(--frame);border-radius:22px;overflow:hidden;background:#fff;padding:3px}
.hero-art{width:100%;height:100%;border-radius:16px;background:radial-gradient(circle at 50% 45%,#fff6c8 0%,#ffb02e 12%,#4a6fc0 35%,#1a2b55 70%,#0d1633 100%)}

.pitch{left:618px;top:91px;width:463px;height:243px;border-radius:28px;background:linear-gradient(#fafafa,#e4e4e4);box-shadow:inset 0 0 0 2px #eee,0 2px 6px rgba(0,0,0,.08);text-align:center;font-family:"Questrial",sans-serif}
.pitch-title{margin-top:32px;font-size:47px;color:#333;letter-spacing:1px;line-height:50px}
.pitch-sub{font-size:29px;color:#333;line-height:34px;margin-left:40px}
.pitch-types{font-size:23px;color:var(--green);line-height:28px;margin-left:40px}
.download{position:absolute;left:48px;top:155px;width:308px;height:54px;border-radius:6px;background:linear-gradient(var(--green-light),var(--green));color:#fff;font-size:27px;line-height:54px;font-weight:700;font-family:"Open Sans",sans-serif;letter-spacing:-1px;white-space:nowrap;overflow:hidden;text-align:right;padding-right:14px}

.intro{left:190px;top:360px;font-size:12.5px;color:#555;white-space:nowrap}
.intro b{font-family:"Questrial",sans-serif;font-weight:400;font-size:28px;color:#666;vertical-align:-3px}

.search{left:117px;top:405px;width:964px;height:30px;border:3px solid #999;border-radius:3px;background:#fff;display:flex}
.search-field{flex:1;font-size:15px;line-height:24px;padding-left:12px;color:#333}
.search-btn{width:92px;background:var(--green);color:#fff;font-size:15px;line-height:24px;text-align:center;display:flex;align-items:center;justify-content:center;gap:6px}

.results-head{left:117px;top:454px;width:964px;height:22px;background:var(--bar);font-size:14px;line-height:22px;padding-left:15px;color:#444}
.order{position:absolute;right:12px;top:0;font-size:11px;color:#555}
.order .g{color:var(--green)}.order .r{color:var(--red)}
.filters{left:117px;top:480px;width:964px;height:19px;background:var(--bar-dark);font-size:11px;line-height:19px;padding-left:8px;color:#eee}
.filters .r{color:var(--red)}.filters .g{color:#1d6e2c}.filters .p{color:var(--pink)}.filters .sp{margin-left:14px}
.pager{left:503px;top:451px;height:22px;background:var(--green);color:#fff;font-size:11px;line-height:22px;padding:0 12px;border-radius:2px;box-shadow:0 2px 3px rgba(0,0,0,.25)}

.results{left:117px;top:508px;width:964px;list-style:none}
.result{height:32px;border-bottom:1px solid var(--line);display:flex;align-items:center;font-size:14px;color:#444;position:relative}
.result strong{font-weight:700;margin-right:6px}
.meta{position:absolute;left:693px;top:0;height:32px;display:flex;align-items:center;font-size:11px;color:#777}
.state{width:14px;height:14px;border-radius:50%;border:2px solid var(--green);position:relative;margin-right:13px}
.state::before,.state.plus::after{content:"";position:absolute;background:var(--green);left:2px;top:4px;width:6px;height:2px}
.state.plus::after{left:4px;top:2px;width:2px;height:6px}
.state.minus{border-color:var(--red)}.state.minus::before{background:var(--red)}
.age{width:70px}.size{width:49px}
.badge{display:inline-block;width:15px;height:15px;color:#fff;font-size:10px;text-align:center;line-height:15px;margin-right:5px}
.badge.p{background:var(--blue-badge)}.badge.s{background:#6fbf3a}
.num{width:61px}

.stats{left:288px;top:776px;font-size:13px;color:#444;letter-spacing:.3px;white-space:nowrap}
.social{left:850px;top:772px;display:flex;gap:7px}
.social span{width:19px;height:19px;border-radius:2px;box-shadow:0 6px 5px -4px rgba(0,0,0,.15)}

.footer{left:0;top:842px;width:1200px;height:58px;display:flex;align-items:center;padding-left:117px;font-size:17px;color:#444;white-space:nowrap}
.footer-brand{display:flex;align-items:center;gap:4px;font-family:"Questrial",sans-serif;font-size:28px;color:var(--ink);margin-right:8px}
.footer-brand i{width:24px;height:24px;border-radius:50%;background:var(--green)}
.footer a{color:var(--green);text-decoration:none}

.popup{background:#fff;border-radius:6px;box-shadow:0 3px 12px rgba(0,0,0,.35);font-size:9px;color:#333;padding:0 14px}
.popup-title{position:absolute;left:50%;transform:translateX(-50%);top:-6px;background:var(--green);color:#fff;font-size:15px;padding:0 12px;line-height:20px;border-radius:2px}
.popup-close{position:absolute;right:5px;top:5px;width:12px;height:12px;border-radius:50%;background:#ddd;color:#666;font-size:9px;text-align:center;line-height:12px}
.popup label{display:block;margin-top:14px}
.popup .field{height:14px;border:1px solid #999;border-radius:8px;margin-top:5px}
.popup .check{display:flex;align-items:center;gap:6px;margin-top:6px;font-size:7px;white-space:nowrap}
.popup .check i{width:9px;height:9px;border:1px solid #666;border-radius:2px}
.popup .check a{color:var(--green)}
.popup .submit{display:block;margin:10px auto 0;width:66px;height:15px;border-radius:8px;background:var(--green);color:#fff;font-size:12px;text-align:center;line-height:15px}
.login{left:300px;top:262px;width:176px;height:195px}
.login .link{display:block;text-align:center;color:var(--green);font-size:7px;margin-top:8px;text-decoration:underline}
.register{left:600px;top:181px;width:176px;height:297px}
</style>
</head>
<body>
<div class="canvas">

  <div class="brand abs">
    <div class="brand-name"><span class="brand-dot"></span>Qentrova</div>
    <div class="brand-tag">torrents search engine</div>
  </div>

  <nav class="nav abs">
    <a href="#">HOME</a><a href="#">Qentrova</a><a href="#" class="active">iSEARCH</a><a href="#">HELP</a><a href="#">PROFILE</a>
  </nav>
  <div class="lang abs">Select Language <span class="lang-select">English</span></div>

  <div class="hero-frame abs"><div class="hero-art" role="img" aria-label="Collage of colourful media thumbnails flying out from a bright centre"></div></div>

  <section class="pitch abs">
    <div class="pitch-title">FIND,GET,ENJOY</div>
    <div class="pitch-sub">A WORLD OF TORRENT FILES</div>
    <div class="pitch-types">Movies, Games, Music, Software, etc.</div>
    <div class="download">DOWNLOAD Qentrova</div>
  </section>

  <p class="intro abs"><b>Qentrova</b> is a new lightweight torrent search engine, it makes incredibly fast use of bandwidth while reducing network problems.</p>

  <div class="search abs">
    <div class="search-field">starforge 3</div>
    <div class="search-btn">
      <svg width="14" height="14" viewBox="0 0 14 14"><circle cx="5.5" cy="5.5" r="4" fill="none" stroke="#fff" stroke-width="2"/><line x1="8.5" y1="8.5" x2="13" y2="13" stroke="#fff" stroke-width="2.4"/></svg>Search
    </div>
  </div>

  <div class="results-head abs">1 - 10 of 20 for “ starforge 3 ” ( 1,155s )
    <span class="order">Order by relevance | <span class="g">date</span> | <span class="g">size</span> | <span class="r">peers</span> | seeds</span>
  </div>
  <div class="pager abs">previous | 1 | 2 | next</div>
  <div class="filters abs">Quality : <span class="r">all</span> | <span class="g">good</span> | <span class="p">bad</span> | <span class="g">verified</span><span class="sp">Search by : <span class="g">filename</span> | <span class="p">titles</span> | <span class="g">data added</span></span></div>

  <ul class="results abs">
    <li class="result"><strong>starforge 3</strong>HD XVD bgfsbsb.225<span class="meta"><i class="state plus"></i><span class="age">3 days ago</span><span class="size">549 MB</span><span class="badge p">P</span><span class="num">10.555</span><span class="badge s">S</span>10.200</span></li>
    <li class="result"><strong>starforge 3</strong>HD XVD bgfsbsb.225<span class="meta"><i class="state plus"></i><span class="age">3 days ago</span><span class="size">549 MB</span><span class="badge p">P</span><span class="num">10.555</span><span class="badge s">S</span>10.200</span></li>
    <li class="result"><strong>starforge 3</strong>HD XVD bgfsbsb.225<span class="meta"><i class="state minus"></i><span class="age">3 days ago</span><span class="size">549 MB</span><span class="badge p">P</span><span class="num">10.555</span><span class="badge s">S</span>10.200</span></li>
    <li class="result"><strong>starforge 3</strong>HD XVD bgfsbsb.225<span class="meta"><i class="state plus"></i><span class="age">3 days ago</span><span class="size">549 MB</span><span class="badge p">P</span><span class="num">10.555</span><span class="badge s">S</span>10.200</span></li>
    <li class="result"><strong>starforge 3</strong>HD XVD bgfsbsb.225<span class="meta"><i class="state plus"></i><span class="age">3 days ago</span><span class="size">549 MB</span><span class="badge p">P</span><span class="num">10.555</span><span class="badge s">S</span>10.200</span></li>
    <li class="result"><strong>starforge 3</strong>HD XVD bgfsbsb.225<span class="meta"><i class="state plus"></i><span class="age">3 days ago</span><span class="size">549 MB</span><span class="badge p">P</span><span class="num">10.555</span><span class="badge s">S</span>10.200</span></li>
    <li class="result"><strong>starforge 3</strong>HD XVD bgfsbsb.225<span class="meta"><i class="state minus"></i><span class="age">3 days ago</span><span class="size">549 MB</span><span class="badge p">P</span><span class="num">10.555</span><span class="badge s">S</span>10.200</span></li>
  </ul>

  <p class="stats abs">velmora &nbsp;15 , 337 , 488 &nbsp;active torrents from 60 , 307 , 316 &nbsp;pages on 33 domains</p>
  <div class="social abs" aria-label="Social links">
    <span style="background:#cfd8e6"></span><span style="background:#f08a24"></span><span style="background:#5bb8e8"></span><span style="background:#3b5a9a"></span><span style="background:#1f6fa8"></span><span style="background:#e5e5e5"></span><span style="background:#3a4f7a"></span><span style="background:#9cc23a"></span><span style="background:#3b8fd0"></span>
  </div>

  <footer class="footer abs">
    <span class="footer-brand"><i></i>Qentrova</span>
    Copyright © 2011 Qentrova. Use of this website constitutes acceptance of our&nbsp;<a href="#">User Agreement</a>&nbsp;and&nbsp;<a href="#">Privacy Policy</a>.
  </footer>

  <form class="popup login abs">
    <span class="popup-title">Login</span><span class="popup-close">×</span>
    <label style="margin-top:34px">Username:</label><div class="field"></div>
    <label>Password:</label><div class="field"></div>
    <div class="check" style="margin-top:12px"><i></i>Remember Me</div>
    <div class="check"><i></i>Forgot Your Password? <a href="#">Click here.</a></div>
    <span class="submit">Submit</span>
    <a class="link" href="#">Register</a>
  </form>

  <form class="popup register abs">
    <span class="popup-title">Register</span><span class="popup-close">×</span>
    <label style="margin-top:54px">Username:</label><div class="field"></div>
    <label>Password:</label><div class="field"></div>
    <label>Retype Password:</label><div class="field"></div>
    <label>E-mail Address:</label><div class="field"></div>
    <div class="check" style="margin-top:18px"><i></i>I agree to the <a href="#">Terms and Conditions.</a></div>
    <span class="submit" style="margin-top:14px">Submit</span>
  </form>

</div>
</body>
</html>
```